BRELWINCare.co.uk - Mental Health Clinic for Child and Adolescents

Updated 29/01/2018***
I am not sure you guys are getting the idea regards to the opening page / homescreen layout. Can you look at the new images I have uploaded (page 5, 6 and 7) These are some of the layouts I like but to incorporate my chosen images, with the BRELWIN commissioner, buttons and a sliding header bar.
I have written a strong brief, I am looking for a website, preferably wordpress as i know they are easy to maintain. I am looking for a one page site, with the top / opening page being full screen image with drop down categories. I have made a rough design, see full brief in word doc attached, there is some freedom to play around with the design aspect but it will need to relay all the content provided. I like a minimal feel. I have also attached some images that may be useful, but will need a new logo for BRELWIN Care. I have attached some logo idea's, it is up to you decide whether you want to use them.
I would prefer the homepage as full screen image, and the categories offered as a drop down or over the main image.
I have also attached linked to some competitors websites:
https://www.vorimant-health.co.uk/
http://www.qlbn.org.uk/
Industry/Entity Type
Clinic
Number of Pages Required
1 page
Font styles to use
Look and feel
Each slider illustrates characteristics of the customer's brand and the style your logo design should communicate.

```html
<!DOCTYPE html>
<html lang="en">
<head>
<meta charset="utf-8">
<title>BRELWIN Care – Child &amp; Adolescent Mental Health Services</title>
<link href="https://fonts.googleapis.com/css2?family=Montserrat:wght@400;500;600;700&display=swap" rel="stylesheet">
<style>
  :root {
    --navy: #233e8f;
    --navy-text: #2a3f8a;
    --lime: #b5d63c;
    --cyan: #45c6e6;
    --white: #ffffff;
    --rule: #c9c9c9;
    --muted: #5a5a5a;
    --logo-blue: #2a7fd4;
  }
  * { margin: 0; padding: 0; box-sizing: border-box; }
  html, body { width: 1200px; height: 774px; overflow: hidden; }
  body { font-family: "Montserrat", Arial, sans-serif; position: relative; background: var(--white); }

  .hero-photo {
    position: absolute; left: 0; top: 0; width: 1200px; height: 774px;
    background:
      linear-gradient(90deg, rgba(60,50,40,.25) 0%, rgba(0,0,0,0) 40%, rgba(0,0,0,0) 60%, rgba(60,50,40,.2) 100%),
      linear-gradient(180deg, #ecebe8 0%, #d9d5cf 35%, #b9ada0 65%, #8f8576 100%);
  }

  .site-header {
    position: absolute; left: 0; top: 0; width: 979px; height: 116px;
    background: rgba(255,255,255,.94);
  }
  .brand { position: absolute; left: 24px; top: 26px; display: flex; align-items: center; gap: 12px; }
  .brand-dot { width: 60px; height: 60px; border-radius: 50%; background: var(--lime); }
  .brand-name { font-weight: 700; font-size: 26px; color: var(--logo-blue); line-height: 1; }
  .brand-sub { font-size: 9px; color: #333; line-height: 1.25; margin-top: 6px; width: 120px; }

  .tagline {
    position: absolute; left: 390px; top: 43px; width: 345px; height: 30px;
    border-top: 1px solid var(--rule); border-bottom: 1px solid var(--rule);
    font-size: 9.5px; letter-spacing: 1.2px; color: var(--muted);
    display: flex; align-items: center; padding-left: 16px;
  }
  .call {
    position: absolute; left: 774px; top: 48px; font-size: 15px; color: var(--navy-text);
    display: flex; align-items: center; gap: 6px;
  }

  .audience {
    position: absolute; top: 372px; width: 440px; text-align: center; color: var(--white);
  }
  .audience--parents { left: 86px; }
  .audience--commissioners { left: 675px; }
  .audience h2 { font-size: 32px; font-weight: 700; letter-spacing: .5px; line-height: 1.1; }
  .audience p { font-size: 14px; line-height: 1.35; margin-top: 8px; }
  .btn-outline {
    display: inline-block; margin-top: 36px; padding: 9px 26px;
    border: 1.5px solid var(--white); border-radius: 20px;
    font-size: 9.5px; letter-spacing: 1px; font-weight: 500; color: var(--white); text-decoration: none;
  }
  .divider { position: absolute; left: 600px; top: 290px; width: 1px; height: 310px; background: rgba(255,255,255,.8); }

  .copyright {
    position: absolute; left: 23px; top: 730px; font-size: 9.5px; letter-spacing: .8px;
    color: var(--white); line-height: 1.4;
  }

  .side-nav {
    position: absolute; left: 979px; top: 0; width: 221px; height: 774px; background: var(--navy);
  }
  .close { position: absolute; left: 23px; top: 45px; }
  .menu { list-style: none; position: absolute; left: 23px; top: 112px; width: 180px; }
  .menu li { font-size: 14.5px; font-weight: 500; color: var(--white); height: 32.5px; display: flex; justify-content: space-between; align-items: center; }
  .menu li.is-active { color: var(--lime); }
  .contact { position: absolute; left: 23px; top: 582px; }
  .contact-phone { font-size: 14.5px; color: var(--lime); font-weight: 500; }
  .contact-email { font-size: 9.5px; letter-spacing: 1px; color: var(--cyan); margin-top: 6px; display: flex; align-items: center; gap: 6px; }
  .hours { font-size: 10.5px; letter-spacing: 1px; color: var(--cyan); margin-top: 24px; line-height: 1.65; }
  .social { position: absolute; left: 23px; top: 716px; display: flex; gap: 12px; }
  .social span { width: 14px; height: 14px; border-radius: 50%; background: var(--cyan); }
</style>
</head>
<body>
  <div class="hero-photo" role="img" aria-label="Photo of a clinician with a clipboard talking with a young person in a bright room"></div>

  <header class="site-header">
    <div class="brand">
      <span class="brand-dot"></span>
      <div>
        <div class="brand-name">BRELWIN</div>
        <div class="brand-sub">Child &amp; Adolescent Mental Health Services</div>
      </div>
    </div>
    <div class="tagline">- ADHD &amp; AUTISM SCREENING WITHIN 24 HOURS.</div>
    <div class="call">Call:
      <svg width="18" height="18" viewBox="0 0 18 18" aria-hidden="true">
        <circle cx="9" cy="9" r="8" fill="none" stroke="#2a3f8a" stroke-width="1.4"/>
        <path d="M6 5.2c.5-.4 1-.3 1.3.2l.7 1.2c.2.4.1.8-.2 1.1l-.5.4c.4.9 1.1 1.7 2 2.1l.4-.5c.3-.3.7-.4 1.1-.2l1.2.7c.5.3.6.8.2 1.3-.7.9-1.7 1.1-2.7.6C7.6 11.2 6.3 9.9 5.5 8.3c-.5-1-.4-2.3.5-3.1z" fill="#2a3f8a"/>
      </svg>
      0203 555 0199</div>
  </header>

  <section class="audience audience--parents">
    <h2>PARENTS</h2>
    <p>Are you looking for a thorough, efficient, highly accurate screening or assessment for your child?</p>
    <a class="btn-outline" href="#contact">CONTACT US</a>
  </section>
  <div class="divider"></div>
  <section class="audience audience--commissioners">
    <h2>COMMISSIONERS</h2>
    <p>Are you looking to reduce waiting times as part of your ADHD or ASD pathway?</p>
    <a class="btn-outline" href="#contact">CONTACT US</a>
  </section>

  <div class="copyright">COPYRIGHT © BRELWIN CARE ©2018.<br>ALL RIGHTS RESERVED.</div>

  <nav class="side-nav">
    <svg class="close" width="30" height="30" viewBox="0 0 30 30" aria-label="Close menu">
      <path d="M2 2L28 28M28 2L2 28" stroke="#fff" stroke-width="2"/>
    </svg>
    <ul class="menu">
      <li class="is-active">Home</li>
      <li>About Us</li>
      <li>Team</li>
      <li>Services
        <svg width="10" height="6" viewBox="0 0 10 6" aria-hidden="true"><path d="M1 1l4 4 4-4" fill="none" stroke="#fff" stroke-width="1.4"/></svg>
      </li>
      <li>Parents</li>
      <li>Commissioners</li>
      <li>Blog</li>
      <li>Contact Us</li>
    </ul>
    <div class="contact" id="contact">
      <div class="contact-phone">P. 0203 555 0199</div>
      <div class="contact-email">
        <svg width="9" height="8" viewBox="0 0 9 8" aria-hidden="true"><path d="M1 3l3.5-2 3.5 2v4H1z" fill="#45c6e6"/></svg>
        EMAIL US</div>
      <div class="hours">OPENING TIME<br>MON TO FRI: 9A.M – 5 P.M</div>
    </div>
    <div class="social" aria-label="Social links">
      <span></span><span></span><span></span><span></span>
    </div>
  </nav>
</body>
</html>
```